Managed IT services business card design

We haven't needed a business card since the founding of the business in 2005. All our clients have been coming through word of mouth. And lately more and more existing clients are requesting for our business cards to pass on to their contacts in recommending us.
So we needing a business card design. We use various innovative solutions and methodologies to provide IT services to small businesses in managing their IT systems. Our role is the same as an in-house, full-time IT Manager for our clients, but outsourced. So we take care of all our clients' IT needs, just as an IT Manager would be expected to perform.
We have a holding website, which we're happy to leave for now. If we can use the same logo would be great - www.lumadesk.com.au
Preferred colours are shades of are white, grey and black.
We pride our business with the following traits: proactive, good service, prompt response, trustworthy.
Target Market(s)
Small businesses of any industry
Industry/Entity Type
Business

```html
<!DOCTYPE html>
<html lang="en">
<head>
<meta charset="utf-8">
<title>lumadesk business card</title>
<link rel="stylesheet" href="https://fonts.googleapis.com/css2?family=Arimo:wght@400&family=Open+Sans:wght@400;600&display=swap">
<style>
  :root {
    --page: #e6e6e6;
    --card: #ffffff;
    --ink: #111111;
    --band-dark: #262626;
    --band-light: #5a5a5a;
    --rule: #3a3a3a;
    --on-dark: #ffffff;
    --on-dark-soft: #e2e2e2;
  }
  * { box-sizing: border-box; margin: 0; padding: 0; }
  html, body {
    width: 1200px; height: 1000px; overflow: hidden;
    background: var(--page);
  }
  .card {
    position: absolute; left: 110px; top: 221px;
    width: 980px; height: 558px;
    background: var(--card);
    box-shadow: 0 10px 30px rgba(0,0,0,.18);
    overflow: hidden;
    font-family: "Open Sans", sans-serif;
  }
  .brand-name {
    position: absolute; left: 0; right: 0; top: 100px;
    text-align: center;
    font-family: "Arimo", sans-serif;
    font-size: 62px; font-weight: 400;
    letter-spacing: 0.28em;
    color: var(--ink);
  }
  .address {
    position: absolute; left: 0; right: 0; top: 266px;
    text-align: center;
    font-size: 22px; color: var(--ink);
  }
  .top-rule {
    position: absolute; left: 0; right: 0; top: 324px; height: 10px;
    background: var(--rule);
  }
  .info-band {
    position: absolute; left: 0; right: 0; top: 344px; bottom: 0;
    background: linear-gradient(180deg, var(--band-dark) 0%, var(--band-light) 55%, var(--band-dark) 100%);
  }
  .notch { position: absolute; left: 0; top: 42px; }
  .person {
    position: absolute; left: 125px; top: 64px; color: var(--on-dark);
  }
  .person-name { font-size: 40px; font-weight: 600; line-height: 1.1; }
  .person-role { font-size: 28px; color: var(--on-dark-soft); line-height: 1; }
  .divider {
    position: absolute; left: 490px; top: 20px; width: 2px; height: 172px;
    background: linear-gradient(180deg, rgba(255,255,255,0), rgba(255,255,255,.75), rgba(255,255,255,0));
  }
  .contacts {
    position: absolute; left: 562px; top: 32px; list-style: none;
  }
  .contact {
    display: flex; align-items: center; height: 52px;
    font-size: 24px; color: var(--on-dark);
  }
  .contact svg { width: 32px; height: 32px; flex: none; }
  .contact .sep {
    width: 2px; height: 28px; background: var(--on-dark); margin: 0 12px 0 14px;
  }
</style>
</head>
<body>
  <main class="card">
    <div class="brand-name">lumadesk</div>
    <div class="address">Quarry Lane, Ballarat</div>
    <div class="top-rule"></div>
    <section class="info-band">
      <svg class="notch" width="52" height="116" viewBox="0 0 52 116"><polygon points="0,0 52,58 0,116" fill="#ffffff"/></svg>
      <div class="person">
        <div class="person-name">Name Title</div>
        <div class="person-role">designation</div>
      </div>
      <div class="divider"></div>
      <ul class="contacts">
        <li class="contact">
          <svg viewBox="0 0 32 32"><rect x="2" y="2" width="28" height="28" rx="6" fill="#fff"/><path d="M11 8c1 0 2 3 2 4s-2 1-2 2c0 2 3 6 5 7 1 0 1-2 2-2s4 1 4 2-1 3-3 3c-6 0-11-7-11-12 0-2 2-4 3-4z" fill="#333"/></svg>
          <span class="sep"></span>+61 400 555 018
        </li>
        <li class="contact">
          <svg viewBox="0 0 32 32"><rect x="2" y="2" width="28" height="28" rx="6" fill="#fff"/><rect x="7" y="11" width="18" height="12" fill="#333"/><path d="M7 11l9 7 9-7" fill="none" stroke="#fff" stroke-width="1.6"/></svg>
          <span class="sep"></span>mail@lumadesk.com.au
        </li>
        <li class="contact">
          <svg viewBox="0 0 32 32"><circle cx="16" cy="16" r="13" fill="#fff"/><g fill="none" stroke="#333" stroke-width="1.6"><circle cx="16" cy="16" r="9"/><ellipse cx="16" cy="16" rx="4" ry="9"/><path d="M7 16h18M9 11h14M9 21h14"/></g></svg>
          <span class="sep"></span>www.lumadesk.com.au
        </li>
      </ul>
    </section>
  </main>
</body>
</html>
```